Business card design for holistic health care clinic

We need a double-sided business card design for our holistic health care clinic that integrates our logo design and also its color scheme. My business is called Valmira. It is an integrative medicine clinic. You have already done the logo for me. Please ensure an elegant and upscale design that is not cluttered, but still has all the necessary information (please see below for details).

Target Market(s)

Wellness, fitness, rehabilitation for educated, well-traveled open-minded clients who are focused on natural, organic, balanced and preventive healthcare and lifestyle.

Industry/Entity Type

Medical

Contact Information for Business Card

Modern, clean.

Number of Pages Required

1 page

Font styles to use
Serif
Sans Serif

Colors

Designer to choose colors to be used in the design.

Requirements
Must have
• Logo on one side, all other information on the other side.
• Other information should include:
• Tobias Wrenfeld - DOE, CPT, LMT
• 4100 East Marrow Drive
• Austin, TX 78119
• 512 555 0148
• 818 555 0192
• info@ValmiraHealth.example
• t.wrenfeld@ValmiraHealth.example
Nice to have
• Darker background on front - but not totally black - shaded/dark gray.

```html
<!DOCTYPE html>
<html lang="en">
<head>
<meta charset="utf-8">
<title>Valmira – Business Card</title>
<link rel="stylesheet" href="https://fonts.googleapis.com/css2?family=Roboto:wght@400;500;700&family=Roboto+Condensed:wght@700&display=swap">
<style>
  :root {
    --backdrop: #5b4838;
    --card-dark: #2a2a2a;
    --card-dark-edge: #333333;
    --brand-blue: #0a8ac6;
    --card-blue: #0b8dca;
    --card-blue-deep: #0682bf;
    --ink-dark: #242424;
    --text-light: #e8e8e8;
    --rule: #bdbdbd;
  }
  * { margin: 0; padding: 0; box-sizing: border-box; }
  html, body { width: 1200px; height: 960px; overflow: hidden; }
  body {
    background: var(--backdrop);
    position: relative;
    font-family: "Roboto", Arial, sans-serif;
  }
  .card {
    position: absolute;
    width: 601px;
    height: 343px;
    border-radius: 22px;
    box-shadow: 0 3px 6px rgba(0,0,0,0.35);
  }
  .card-front {
    left: 314px; top: 114px;
    background: linear-gradient(180deg, var(--card-dark-edge), var(--card-dark));
  }
  .card-back {
    left: 311px; top: 472px;
    background: linear-gradient(180deg, var(--card-blue), var(--card-blue-deep));
  }
  .brand {
    position: absolute;
    text-align: right;
  }
  .front-brand { right: 36px; top: 66px; }
  .brand-name {
    font-family: "Roboto", Arial, sans-serif;
    font-weight: 700;
    letter-spacing: 1px;
    line-height: 1;
  }
  .front-brand .brand-name { color: var(--brand-blue); font-size: 52px; }
  .brand-descriptor {
    font-weight: 500;
    line-height: 1;
  }
  .front-brand .brand-descriptor { color: var(--brand-blue); font-size: 15px; margin-top: 6px; }

  .holder {
    position: absolute;
    left: 33px; top: 186px;
    font-family: "Roboto Condensed", "Arial Narrow", sans-serif;
    font-weight: 700;
    color: var(--brand-blue);
    text-transform: uppercase;
  }
  .holder-name { font-size: 20px; }
  .holder-credentials { font-size: 12px; }
  .rule {
    position: absolute;
    left: 33px; right: 36px; top: 222px;
    height: 1px;
    background: var(--rule);
  }
  .contact-list {
    position: absolute;
    left: 34px; top: 237px;
    list-style: none;
    color: var(--text-light);
    font-size: 14px;
  }
  .contact-list li {
    display: flex; align-items: center;
    height: 19px;
  }
  .contact-list svg { width: 14px; height: 14px; margin-right: 9px; fill: var(--brand-blue); }
  .address {
    position: absolute;
    right: 36px; top: 275px;
    text-align: right;
    color: var(--text-light);
    font-size: 14px;
    font-style: normal;
    line-height: 19px;
  }

  .back-brand {
    left: 0; right: 0; top: 142px;
    text-align: center;
  }
  .back-brand .brand-name { color: var(--ink-dark); font-size: 62px; }
  .back-brand .brand-descriptor { color: var(--ink-dark); font-size: 17px; margin-top: 6px; }
  .tagline {
    position: absolute;
    left: 0; right: 0; top: 282px;
    text-align: center;
    color: var(--ink-dark);
    font-size: 14px;
  }
</style>
</head>
<body>
  <section class="card card-front">
    <div class="brand front-brand">
      <div class="brand-name">VALMIRA</div>
      <div class="brand-descriptor">Integrative Holistic Medicine</div>
    </div>

    <div class="holder">
      <span class="holder-name">Tobias Wrenfeld</span>
      <span class="holder-credentials">- DOE, CPT, LMT</span>
    </div>
    <div class="rule"></div>

    <ul class="contact-list">
      <li>
        <svg viewBox="0 0 24 24" aria-hidden="true"><path d="M6.6 10.8a15.1 15.1 0 0 0 6.6 6.6l2.2-2.2c.3-.3.7-.4 1-.2 1.1.4 2.3.6 3.6.6.6 0 1 .4 1 1V20c0 .6-.4 1-1 1A17 17 0 0 1 3 4c0-.6.4-1 1-1h3.5c.6 0 1 .4 1 1 0 1.3.2 2.5.6 3.6.1.3 0 .7-.2 1z"/></svg>
        512 555 0148
      </li>
      <li>
        <svg viewBox="0 0 24 24" aria-hidden="true"><path d="M7 1h10a2 2 0 0 1 2 2v18a2 2 0 0 1-2 2H7a2 2 0 0 1-2-2V3a2 2 0 0 1 2-2zm0 3v15h10V4zm5 16.2a.9.9 0 1 0 0 1.8.9.9 0 0 0 0-1.8z"/></svg>
        818 555 0192
      </li>
      <li>
        <svg viewBox="0 0 24 24" aria-hidden="true"><path d="M2 5h20v14H2zm2 2v.4l8 5 8-5V7zm0 2.8V17h16V9.8l-8 5z"/></svg>
        t.wrenfeld@ValmiraHealth.example
      </li>
      <li>
        <svg viewBox="0 0 24 24" aria-hidden="true"><path d="M12 2a10 10 0 1 0 0 20 10 10 0 0 0 0-20zm-1 17.9A8 8 0 0 1 4.1 10L9 15v1a2 2 0 0 0 2 2zm6.9-2.5A2 2 0 0 0 16 16h-1v-3a1 1 0 0 0-1-1H8v-2h2a1 1 0 0 0 1-1V7h2a2 2 0 0 0 2-2v-.4a8 8 0 0 1 2.9 12.8z"/></svg>
        www.ValmiraHealth.example
      </li>
    </ul>

    <address class="address">
      4100 East Marrow Drive<br>
      Austin, TX 78119
    </address>
  </section>

  <section class="card card-back">
    <div class="brand back-brand">
      <div class="brand-name">VALMIRA</div>
      <div class="brand-descriptor">Integrative Holistic Medicine</div>
    </div>
    <p class="tagline">it’s all about you – your health, your objectives</p>
  </section>
</body>
</html>
```